Sell the dream! Property investment proposal document

We are looking for a proposal document which outlines our vision for property development. The purpose of the document is to raise investment from investors - sell the dream!
Brief summary:
Kestrel Dwellings Developments, is an emerging New Zealand property investment company with a focus on providing unique property investment opportunities.
Our expertise and capabilities in architectural modular homes provide us with a remarkable advantage in tackling the development of properties that are typically considered challenging, remote, or uniquely positioned.
Our specialization in this niche sector of property development not only sets us apart from competitors, but also paves the way for lucrative investment opportunities in the New Zealand property market.
Feel free to use any images from www.kestreldwellings.co.nz
Target Market(s)
investors for a unique property development opportunity
Industry/Entity Type
luxury property development in unique locations throughout New Zealand
Colors
Designer to choose only greyscale colors for use in the design.
Look and feel

```html
<!DOCTYPE html>
<html lang="en">
<head>
<meta charset="utf-8">
<title>Kestrel Dwellings – Investment Proposal Spreads</title>
<link href="https://fonts.googleapis.com/css2?family=Poppins:wght@300;400;600;800&display=swap" rel="stylesheet">
<style>
:root{
  --canvas:#e0e0e0;
  --page:#1e1e1e;
  --page-alt:#2b2b2b;
  --band:#474747;
  --white:#ffffff;
  --text:#d6d6d6;
  --muted:#9a9a9a;
  --tag:#4a4a4a;
}
*{margin:0;padding:0;box-sizing:border-box}
html,body{width:1034px;height:1200px;overflow:hidden;background:var(--canvas);font-family:'Poppins',sans-serif;color:var(--white)}
.canvas{position:relative;width:1034px;height:1200px}
.spread{position:absolute;background:var(--page);box-shadow:0 6px 14px rgba(0,0,0,.35);overflow:hidden}
.spread > *{position:absolute}
.photo{border:1px solid #555}
.brand{font-family:'Poppins',sans-serif;font-weight:400;color:var(--white);letter-spacing:-0.5px;line-height:1;white-space:nowrap}

/* cover */
.cover{left:63px;top:79px;width:914px;height:322px}
.cover .band{top:0;width:41px;height:322px;background:var(--band)}
.cover .band--left{left:0}
.cover .band--right{left:873px}
.cover .photo{top:73px;width:403px;height:148px}
.cover .brand--top{left:580px;width:210px;text-align:center;top:26px;font-size:34px}
.cover .brand--foot{left:73px;top:241px;font-size:24px}
.contact{font-size:9.5px;color:var(--text);display:flex;align-items:center;gap:4px;white-space:nowrap}
.contact--phone{left:172px;top:254px}
.contact--web{left:258px;top:248px;font-size:5.5px;line-height:9px;display:block}
.contact--web span{display:flex;align-items:center;gap:4px}
.dot{width:5px;height:5px;border-radius:50%;background:#666;display:inline-block}
.tagline-block{left:483px;width:403px;top:226px;text-align:center}
.headline{font-size:23px;line-height:1;letter-spacing:-0.3px}
.headline .light{font-weight:300;color:#bdbdbd}
.headline .bold{font-weight:800;color:var(--white)}
.tagline{font-size:6.6px;font-weight:300;color:var(--text);margin-top:6px}
.cover-url{font-size:7px;font-weight:600;letter-spacing:2.2px;margin-top:10px;color:var(--white)}

/* inner spreads */
.inner{left:51px;width:931px;height:328px}
.spread--one{top:434px}
.spread--two{top:795px}
.section-title{font-size:10px;letter-spacing:3px;font-weight:400;white-space:nowrap;color:var(--white)}
.section-title b{font-weight:600;color:var(--muted)}
.body-copy{font-size:4.3px;line-height:1.42;color:var(--text);font-weight:300}
.body-copy p{margin-bottom:4.2px}
.page-brand{font-size:17px;top:262px}
.folio{top:272px;font-size:5.6px;letter-spacing:1.4px;color:var(--text);display:flex;align-items:center;gap:6px;white-space:nowrap}
.folio .num{background:var(--tag);color:var(--text);font-size:5px;letter-spacing:0;padding:1px 2px}
.alt-panel{background:var(--page-alt)}
</style>
</head>
<body>
<div class="canvas">

  <section class="spread cover">
    <div class="band band--left"></div>
    <div class="band band--right"></div>
    <div class="photo" style="left:27px;background:linear-gradient(180deg,#8d8f88 0%,#6f6d58 35%,#4b5a2c 60%,#3a3a22 100%)" role="img" aria-label="Interior view through glass doors over green hills and a harbour"></div>
    <div class="photo" style="left:483px;background:linear-gradient(180deg,#b7aa90 0%,#8b7b55 25%,#5a5a2a 55%,#3b3520 100%)" role="img" aria-label="Aerial view of a dark modular home on coastal farmland at golden hour"></div>
    <div class="brand brand--top">Kestrel</div>
    <div class="brand brand--foot">Kestrel</div>
    <div class="contact contact--phone">
      <svg width="8" height="8" viewBox="0 0 24 24" fill="none" stroke="#bbb" stroke-width="2"><path d="M5 3h4l2 5-2.5 1.5a11 11 0 0 0 6 6L16 13l5 2v4a2 2 0 0 1-2 2A17 17 0 0 1 3 5a2 2 0 0 1 2-2z"/></svg>
      09 555 0142
    </div>
    <div class="contact contact--web">
      <span><i class="dot"></i>sales@kestreldwellings.co.nz</span>
      <span><i class="dot"></i>www.kestreldwellings.co.nz</span>
    </div>
    <div class="tagline-block">
      <div class="headline"><span class="light">SELL</span><span class="bold">THE DREAM!</span></div>
      <div class="tagline">Homes Developments, is an emerging New Zealand property investment company</div>
      <div class="cover-url">www.kestreldwellings.co.nz</div>
    </div>
  </section>

  <section class="spread inner spread--one">
    <div style="left:254px;top:0;width:212px;height:258px;background:linear-gradient(180deg,#a9b3bd 0%,#c9c2a8 45%,#8e8a7c 65%,#5b564d 100%)" role="img" aria-label="Cantilevered glass house on a cliff edge overlooking the sea at sunset"></div>
    <div class="alt-panel" style="left:254px;top:258px;width:212px;height:70px"></div>

    <h2 class="section-title" style="left:48px;top:46px">BUSINESS <b>OVERVIEW</b></h2>
    <div class="body-copy" style="left:50px;top:70px;width:141px">
      <p>Kestrel Dwellings Developments, is an emerging New Zealand property investment company with a focus on providing unique property investment opportunities.</p>
      <p>Our expertise and capabilities in architectural modular homes provide us with a remarkable advantage in tackling the development of properties that are typically considered challenging, remote, or uniquely positioned.</p>
      <p>As a company, with 48 employees boasting a wealth of experience in handling complex architectural projects, making us well-equipped to navigate the intricacies and demands of such ventures.</p>
      <p>This advantage allows us to not only execute projects efficiently but also to deliver exceptional results within condensed time frames.</p>
      <p>By capitalizing on our ability to develop difficult, remote, or one-of-a-kind properties swiftly and effectively, Kestrel Dwellings Developments offers investors a rare chance to engage in projects that promise exceptional profitability in the New Zealand property market.</p>
      <p>Our specialization in this niche sector of property development not only sets us apart from competitors, but also paves the way for lucrative investment opportunities in the New Zealand property market.</p>
    </div>
    <div class="brand page-brand" style="left:48px">Kestrel</div>
    <div class="folio" style="left:289px">www.kestreldwellings.co.nz <span class="num">01</span></div>

    <h2 class="section-title" style="left:518px;top:46px">BUSINESS <b>ORIGINS</b></h2>
    <div class="body-copy" style="left:518px;top:70px;width:160px">
      <p>Kestrel Dwellings Developments, is an emerging New Zealand property investment company with a focus on providing unique property investment opportunities.</p>
      <p>Our expertise and capabilities in architectural modular homes provide us with a remarkable advantage in tackling the development of properties that are typically considered challenging, remote, or uniquely positioned.</p>
      <p>As a company, with 48 employees boasting a wealth of experience in handling complex architectural projects, making us well-equipped to navigate the intricacies and demands of such ventures.</p>
      <p>This advantage allows us to not only execute projects efficiently but also to deliver exceptional results within condensed time frames.</p>
      <p>By capitalizing on our ability to develop difficult, remote, or one-of-a-kind properties swiftly and effectively, Kestrel Dwellings Developments offers investors a rare chance to engage in projects that promise exceptional profitability in the New Zealand property market.</p>
      <p>Our specialization in this niche sector of property development not only sets us apart from competitors, but also paves the way for lucrative investment opportunities in the New Zealand property market.</p>
    </div>
    <div class="photo" style="left:737px;top:40px;width:145px;height:97px;background:linear-gradient(180deg,#c9d8e6 0%,#7fa3c4 45%,#40526a 65%,#1c1c1c 100%)" role="img" aria-label="Living room with lounge chairs facing a wide ocean view"></div>
    <div class="photo" style="left:737px;top:149px;width:145px;height:96px;background:linear-gradient(180deg,#d8dfe4 0%,#9fb1c0 35%,#6c8a4a 65%,#8d7f6e 100%)" role="img" aria-label="Open glass doors onto a deck overlooking green hills and water"></div>
    <div class="brand page-brand" style="left:514px">Kestrel</div>
    <div class="folio" style="left:755px">www.kestreldwellings.co.nz <span class="num">01</span></div>
  </section>

  <section class="spread inner spread--two">
    <div class="photo" style="left:50px;top:48px;width:365px;height:110px;background:linear-gradient(180deg,#a89c80 0%,#7a7048 30%,#545a28 60%,#34301c 100%)" role="img" aria-label="Dark modular home on coastal farmland at golden hour"></div>
    <h2 class="section-title" style="left:48px;top:178px">COMPETITIVE <b>ADVANTAGE</b></h2>
    <div class="body-copy" style="left:50px;top:198px;width:372px">
      <p>Our competitive advantage lies in the uniqueness of our property investment opportunities. Unlike traditional real estate companies, we focus on offering properties that are not only profitable but also aesthetically pleasing and unique. By catering to the tastes of architecture lovers, we set ourselves apart from the competition and attract a niche market of customers who appreciate the artistry and design of our projects.</p>
      <p>Additionally, the streamlined and condensed timelines facilitated by our modular approach provide quicker returns on investment.</p>
    </div>
    <div class="brand page-brand" style="left:48px">Kestrel</div>
    <div class="folio" style="left:289px">www.kestreldwellings.co.nz <span class="num">01</span></div>

    <h2 class="section-title" style="left:518px;top:46px">FINANCIAL <b>SUMMARY</b></h2>
    <div class="body-copy" style="left:518px;top:70px;width:155px">
      <p>In terms of financial projections, with each development, we anticipate a profit of 10%-20% which will be project dependent.</p>
      <p>This growth is fueled by the increasing demand for unique property investments in New Zealand and our ability to deliver high-quality services to the market in a condensed time frame, with heavily controlled costs.</p>
      <p>With a solid business model and a dedicated team, we are confident in our ability to achieve success and establish Kestrel Dwellings Investments as a trusted name in the industry.</p>
      <p>New Zealand's property market has been experiencing steady growth over the years, making it an attractive destination for property investors. With its beautiful landscapes and strong economy, New Zealand offers a diverse range of investment opportunities for both local and international investors. The demand for quality properties in prime locations continues to rise, creating a favorable environment for property investment companies like ours that can lean on our modular benefits of being able to reach unique and remote locations.</p>
    </div>
    <div class="photo" style="left:738px;top:41px;width:144px;height:210px;background:linear-gradient(180deg,#3a3a3a 0%,#9a9a94 30%,#8c8678 60%,#2e2e2e 100%)" role="img" aria-label="Corner window room with a lounge chair overlooking rugged mountains"></div>
    <div class="brand page-brand" style="left:514px">Kestrel</div>
    <div class="folio" style="left:755px">www.kestreldwellings.co.nz <span class="num">01</span></div>
  </section>

</div>
</body>
</html>
```